Flat Belly Design Graphics for Social

I want to create 9 social media graphics (new Instagram size 4:5 (1080 x 1350 pixels) focusing on our Flat Belly Graphics, using the pics attached. Use the attached pics, NO RANDOM STOCK PHOTOGRAPHY. For the color scheme of the graphics, the color palette is attached. YOU MUST POST ALL 9 GRAPHICS IN ONE ENTRY.
Using the 3 titles below, create one set of graphics. 1) with all text, then for the others, use the pictures as detailed below in IMPORTANT:
1. Ten-Week Bright Morning Reboot
2. The Quick Garden Kitchen Menu Guide
3. Studio Habits for Lasting Energy Past Midlife - Zero Gym Needed
IMPORTANT:
Only use RK Pic 1 and RK Pic 2 with the title, Ten-Week Bright Morning Reboot
Only use meal plan1 and meal plan2 pics with the title, Quick Garden Kitchen Menu Guide
Only use studio habits 1 and studio habits 2 pics with the title, Studio Habits for Lasting Energy Past Midlife - Zero Gym Needed
women over 40

```html
<!DOCTYPE html>
<html lang="en">
<head>
<meta charset="utf-8">
<title>Social Graphics Set – Women Over 40</title>
<link href="https://fonts.googleapis.com/css2?family=Anton&family=Oswald:wght@500;700&family=Great+Vibes&family=Playfair+Display:wght@600&display=swap" rel="stylesheet">
<style>
:root{
  --pink:#e59bb0;
  --rose:#d0708c;
  --blush:#f8e0e6;
  --shell:#fbeef1;
  --green:#1f4b3f;
  --deep-green:#143a30;
  --white:#ffffff;
  --gold:#d9b36a;
}
*{box-sizing:border-box;margin:0;padding:0}
html,body{width:1200px;height:910px;overflow:hidden;background:var(--white)}
.sheet{
  width:1200px;height:910px;
  display:grid;
  grid-template-columns:repeat(5,235px);
  grid-template-rows:repeat(3,290px);
  column-gap:5px;row-gap:10px;
  padding:8px 0 0 4px;
}
.tile{
  position:relative;overflow:hidden;
  background:radial-gradient(circle at 50% 45%,var(--shell) 0%,var(--blush) 55%,#f2c9d3 100%);
  font-family:'Oswald',sans-serif;
}
.tile .swirl{position:absolute;inset:0;width:100%;height:100%;pointer-events:none}
.content{position:absolute;inset:0;display:flex;flex-direction:column;align-items:center;text-align:center}
.condensed{font-family:'Oswald',sans-serif;font-weight:700;font-style:italic;line-height:.95;letter-spacing:-.5px}
.script{font-family:'Great Vibes',cursive;line-height:1}
.serif{font-family:'Playfair Display',serif;font-weight:600;line-height:1}
.heavy{font-family:'Anton',sans-serif;line-height:1}
.white{color:var(--white);text-shadow:0 1px 2px rgba(120,50,70,.45)}
.pink{color:var(--pink)}
.rose{color:var(--rose)}
.green{color:var(--green)}
.photo{position:absolute}
.photo-woman{background:linear-gradient(180deg,#d8b5a3 0%,#f5f0ea 45%,#2a2a2a 100%)}
.photo-duo{background:linear-gradient(135deg,#c99378 0%,#f3e6dc 55%,#b98a70 100%)}
.photo-duo-blue{background:linear-gradient(135deg,#6cc7d8 0%,#d9b7a6 50%,#6cc7d8 100%)}
.photo-food{background:linear-gradient(135deg,#3c2a20 0%,#7f4b2a 40%,#c8532f 70%,#4d7a2e 100%)}
.circle{border-radius:50%}
.bar{position:absolute;left:42px;right:42px;bottom:56px;height:5px;background:var(--green)}
.blob-green{position:absolute;background:var(--green)}
</style>
</head>
<body>
<svg width="0" height="0" style="position:absolute" aria-hidden="true">
  <defs>
    <symbol id="corner-curves" viewBox="0 0 235 290">
      <path d="M150 0 C200 10 230 40 235 90 L235 0 Z" fill="#1f4b3f"/>
      <path d="M120 0 C170 6 205 22 225 60 C200 30 165 14 120 8 Z" fill="#e59bb0"/>
      <path d="M0 200 C10 240 40 270 90 290 L0 290 Z" fill="#1f4b3f"/>
      <path d="M0 160 C20 220 60 260 130 290 L90 290 C40 270 10 235 0 200 Z" fill="#e59bb0" opacity=".8"/>
      <path d="M235 200 C200 230 180 260 170 290 L235 290 Z" fill="#e59bb0" opacity=".55"/>
      <path d="M30 20 C60 0 90 0 110 0 L0 0 L0 60 C8 42 16 30 30 20 Z" fill="#e59bb0" opacity=".5"/>
    </symbol>
  </defs>
</svg>

<main class="sheet">

  <!-- 1 -->
  <section class="tile">
    <svg class="swirl"><use href="#corner-curves"/></svg>
    <div class="content" style="justify-content:center;gap:2px;transform:rotate(-3deg)">
      <div class="heavy green" style="font-size:58px">EXTRA</div>
      <div class="heavy rose" style="font-size:52px">DESIGNS</div>
    </div>
    <div class="bar"></div>
  </section>

  <!-- 2 -->
  <section class="tile">
    <svg class="swirl"><use href="#corner-curves"/></svg>
    <div class="content" style="padding-top:22px">
      <div class="condensed white" style="font-size:30px">Ten-Week</div>
      <div class="condensed" style="font-size:30px"><span class="pink">Bright</span> <span class="green">Morning</span></div>
      <div class="script green" style="font-size:34px">Reboot</div>
    </div>
    <div class="photo photo-woman" role="img" aria-label="Smiling woman in a white crop top pointing at her waist" style="left:60px;right:60px;top:140px;bottom:0;border-radius:50px 50px 0 0"></div>
  </section>

  <!-- 3 -->
  <section class="tile">
    <svg class="swirl"><use href="#corner-curves"/></svg>
    <div class="content" style="padding-top:38px">
      <div class="condensed green" style="font-size:20px;font-style:normal">THE QUICK GARDEN</div>
      <div class="condensed green" style="font-size:24px;font-style:normal">KITCHEN MENU</div>
      <div class="script rose" style="font-size:30px">Guide</div>
    </div>
    <div class="photo photo-food" role="img" aria-label="Fresh vegetables, fruit and fish around a meal plan notepad" style="left:24px;right:24px;top:124px;height:122px"></div>
  </section>

  <!-- 4 -->
  <section class="tile" style="background:var(--blush)">
    <svg class="swirl" viewBox="0 0 235 290" preserveAspectRatio="none">
      <path d="M0 0 L235 0 L235 120 C180 150 120 130 60 150 C30 160 10 140 0 130 Z" fill="#e59bb0"/>
      <path d="M0 40 C60 60 80 20 140 40 C190 55 210 100 235 90 L235 150 C190 170 140 130 90 150 C50 165 20 140 0 150 Z" fill="#1f4b3f"/>
      <path d="M0 250 C60 200 150 280 235 210 L235 290 L0 290 Z" fill="#d0708c"/>
      <path d="M120 280 C170 250 200 220 230 200" stroke="#d9b36a" fill="none" stroke-width="1"/>
    </svg>
    <div class="photo photo-woman" role="img" aria-label="Smiling woman in a white crop top pointing at her waist" style="left:60px;right:60px;top:8px;height:130px;border-radius:0 0 40px 40px"></div>
    <div class="content" style="justify-content:flex-end;padding-bottom:52px">
      <div class="serif" style="font-size:32px"><span class="green">TEN-</span><span class="rose">WEEK</span></div>
      <div style="display:flex;align-items:baseline;gap:6px"><span class="script green" style="font-size:30px">Bright</span><span class="serif green" style="font-size:22px">MORNING</span></div>
      <div class="serif rose" style="font-size:24px">REBOOT</div>
    </div>
  </section>

  <!-- 5 -->
  <section class="tile">
    <div class="photo photo-duo" role="img" aria-label="Two women sharing a whispered secret, softly faded" style="inset:0;opacity:.45"></div>
    <svg class="swirl"><use href="#corner-curves"/></svg>
    <div class="content" style="justify-content:center;gap:1px">
      <div class="condensed white" style="font-size:30px">Studio Habits for</div>
      <div class="condensed pink" style="font-size:32px">Lasting Energy</div>
      <div class="script green" style="font-size:34px">Past Midlife</div>
      <div class="condensed green" style="font-size:17px;margin-top:4px">- Zero Gym Needed</div>
    </div>
  </section>

  <!-- 6 -->
  <section class="tile">
    <svg class="swirl"><use href="#corner-curves"/></svg>
    <div class="content" style="padding-top:22px;transform:rotate(-3deg)">
      <div class="condensed green" style="font-size:22px">STUDIO HABITS FOR</div>
      <div class="condensed green" style="font-size:22px">LASTING ENERGY</div>
      <div class="condensed rose" style="font-size:28px">PAST MIDLIFE</div>
      <div class="condensed green" style="font-size:12px">- ZERO GYM NEEDED</div>
    </div>
    <div class="photo photo-duo-blue" role="img" aria-label="Two women whispering against a blue backdrop" style="left:28px;right:28px;top:130px;height:146px;border:2px solid var(--green)"></div>
  </section>

  <!-- 7 -->
  <section class="tile">
    <svg class="swirl"><use href="#corner-curves"/></svg>
    <div class="content" style="justify-content:center;gap:2px">
      <div class="condensed white" style="font-size:30px">Studio Habits</div>
      <div class="condensed white" style="font-size:30px">for Lasting</div>
      <div class="condensed pink" style="font-size:34px">Energy</div>
      <div class="script green" style="font-size:36px">Past Midlife</div>
      <div class="condensed green" style="font-size:18px;margin-top:6px">- Zero Gym Needed</div>
    </div>
  </section>

  <!-- 8 -->
  <section class="tile" style="background:var(--blush)">
    <svg class="swirl" viewBox="0 0 235 290" preserveAspectRatio="none">
      <path d="M0 170 C50 120 110 150 160 120 C200 95 220 80 235 70 L235 290 L0 290 Z" fill="#1f4b3f"/>
      <path d="M0 140 C40 110 80 120 110 150 L0 200 Z" fill="#d0708c"/>
      <path d="M100 290 C150 260 200 250 235 220 L235 290 Z" fill="#e59bb0"/>
      <path d="M180 0 C200 20 225 30 235 30 L235 0 Z" fill="#1f4b3f"/>
    </svg>
    <div class="content" style="padding-top:28px;align-items:flex-start;padding-left:18px;text-align:left">
      <div class="condensed green" style="font-size:19px;font-style:normal">STUDIO HABITS FOR</div>
      <div class="condensed" style="font-size:19px;font-style:normal"><span class="green">LASTING ENERGY</span> <span class="rose">PAST MIDLIFE</span></div>
      <div class="condensed green" style="font-size:19px;font-style:normal">- ZERO GYM NEEDED</div>
    </div>
    <div class="photo photo-duo-blue circle" role="img" aria-label="Two women whispering, framed in a circle" style="left:52px;top:110px;width:130px;height:130px;border:3px solid var(--pink)"></div>
  </section>

  <!-- 9 -->
  <section class="tile">
    <svg class="swirl"><use href="#corner-curves"/></svg>
    <div class="content" style="padding-top:36px">
      <div class="condensed white" style="font-size:26px">Studio Habits</div>
      <div class="condensed white" style="font-size:26px">for Lasting</div>
      <div class="condensed pink" style="font-size:28px">Energy</div>
      <div class="script green" style="font-size:30px">Past Midlife</div>
      <div class="condensed green" style="font-size:15px;margin-top:2px">- Zero Gym Needed</div>
    </div>
    <div class="photo photo-duo circle" role="img" aria-label="Two women whispering, framed in a circle" style="left:72px;top:188px;width:92px;height:92px;border:2px solid var(--pink)"></div>
  </section>

  <!-- 10 -->
  <section class="tile">
    <svg class="swirl"><use href="#corner-curves"/></svg>
    <div class="content" style="padding-top:34px">
      <div class="condensed white" style="font-size:24px">Studio Habits</div>
      <div class="condensed pink" style="font-size:24px">for Lasting</div>
      <div class="condensed green" style="font-size:28px">Energy</div>
    </div>
    <div class="photo photo-duo" role="img" aria-label="Two women sharing a whispered secret" style="left:44px;right:44px;top:122px;height:108px"></div>
    <div class="content" style="justify-content:flex-end;padding-bottom:30px">
      <div class="script green" style="font-size:24px">Past Midlife, Zero Gym</div>
    </div>
  </section>

  <!-- 11 -->
  <section class="tile">
    <svg class="swirl"><use href="#corner-curves"/></svg>
    <div class="photo photo-duo" role="img" aria-label="Two women sharing a whispered secret" style="left:0;right:0;top:130px;bottom:0;clip-path:ellipse(75% 90% at 50% 100%)"></div>
    <div class="content" style="padding-top:20px">
      <div class="script white" style="font-size:26px">Studio Habits</div>
      <div class="script white" style="font-size:26px">for Lasting Energy</div>
      <div class="script white" style="font-size:26px">Past Midlife</div>
      <div class="condensed green" style="font-size:15px;margin-top:2px">- Zero Gym Needed</div>
    </div>
  </section>

  <!-- 12 -->
  <section class="tile">
    <svg class="swirl"><use href="#corner-curves"/></svg>
    <div class="photo photo-woman" role="img" aria-label="Smiling woman in a white crop top pointing at her waist" style="left:45px;right:45px;top:80px;bottom:0;border-radius:60px 60px 0 0"></div>
    <div class="content" style="padding-top:30px">
      <div class="condensed" style="font-size:36px;font-style:normal;color:var(--pink);-webkit-text-stroke:1px var(--rose)">TEN-WEEK</div>
      <div class="condensed" style="font-size:36px;font-style:normal"><span style="color:var(--white);-webkit-text-stroke:1px var(--pink)">BRIGHT</span> <span class="green">MORNING</span></div>
      <div class="script green" style="font-size:44px;margin-top:8px">Reboot</div>
    </div>
  </section>

  <!-- 13 -->
  <section class="tile">
    <svg class="swirl"><use href="#corner-curves"/></svg>
    <div class="photo photo-duo" role="img" aria-label="Two women sharing a whispered secret" style="left:40px;right:40px;top:0;height:110px;border-radius:0 0 80px 80px;opacity:.8"></div>
    <div class="content" style="justify-content:center;padding-top:40px;gap:1px">
      <div class="condensed white" style="font-size:30px">Studio Habits</div>
      <div class="condensed white" style="font-size:30px">for Lasting</div>
      <div class="condensed pink" style="font-size:32px">Energy</div>
      <div class="script green" style="font-size:34px">Past Midlife</div>
      <div class="condensed green" style="font-size:17px;margin-top:6px">- Zero Gym Needed</div>
    </div>
  </section>

  <!-- 14 -->
  <section class="tile">
    <svg class="swirl"><use href="#corner-curves"/></svg>
    <div class="content" style="padding-top:44px">
      <div class="script green" style="font-size:24px">Studio Habits</div>
      <div class="condensed green" style="font-size:17px;font-style:normal">for Lasting Energy Past Midlife</div>
      <div class="condensed green" style="font-size:11px">- Zero Gym Needed</div>
    </div>
    <div class="photo photo-duo" role="img" aria-label="Two women sharing a whispered secret" style="left:0;right:0;top:112px;height:150px"></div>
  </section>

  <!-- 15 -->
  <section class="tile">
    <svg class="swirl"><use href="#corner-curves"/></svg>
    <div class="content" style="justify-content:center;gap:1px">
      <div class="condensed white" style="font-size:30px">Studio Habits</div>
      <div class="condensed white" style="font-size:30px">for Lasting</div>
      <div class="condensed pink" style="font-size:32px">Energy</div>
      <div class="script green" style="font-size:34px">Past Midlife</div>
      <div class="condensed green" style="font-size:17px;margin-top:6px">- Zero Gym Needed</div>
    </div>
  </section>

</main>
</body>
</html>
```